Birchline Septic Solutions

Would like to see some single sided ones but would also like to see some double sided with one sided only being the logo. Owners name is Colin Vandro. Phone number is 555-214-0387
Services are pumping, inspections, installs, and repairs

Contact Information for Business Card

555-241-0387 Colin Vandro Maple Hollow, OH

```html
<!DOCTYPE html>
<html lang="en">
<head>
<meta charset="utf-8">
<title>Birchline Septic Solutions – Business Card</title>
<link rel="stylesheet" href="https://fonts.googleapis.com/css2?family=Montserrat:wght@500;600;700;800&display=swap">
<style>
  :root {
    --backdrop: #9b9b9b;
    --card-white: #ffffff;
    --card-dark: #1d1d1d;
    --ink: #111111;
    --teal: #2dbdb8;
    --white: #ffffff;
    --scene-light: #d9d9d9;
    --scene-dark: #3a3a3a;
  }
  * { margin: 0; padding: 0; box-sizing: border-box; }
  html, body {
    width: 1093px; height: 1200px; overflow: hidden;
    background: var(--backdrop);
    font-family: "Montserrat", Arial, sans-serif;
  }
  .card {
    position: absolute; left: 264px; width: 580px; height: 357px; overflow: hidden;
  }
  .card--front { top: 226px; background: var(--card-white); }
  .card--back { top: 620px; background: var(--card-dark); }

  /* Front */
  .scenery {
    position: absolute; left: 0; top: 222px; width: 580px; height: 135px;
    background: linear-gradient(90deg, var(--scene-light) 0%, var(--scene-dark) 100%);
  }
  .brand {
    position: absolute; left: 32px; top: 30px; width: 220px;
    color: var(--ink); font-weight: 800; text-transform: uppercase;
    font-size: 24px; line-height: 1.1; letter-spacing: 0.5px;
  }
  .owner {
    position: absolute; right: 38px; top: 35px;
    font-weight: 800; font-size: 19px; color: var(--ink); text-transform: uppercase;
  }
  .owner-tab {
    position: absolute; right: 0; top: 34px; width: 26px; height: 20px;
    background: var(--teal); clip-path: polygon(40% 0, 100% 0, 100% 100%, 0 100%);
  }
  .contact-band {
    position: absolute; left: 0; top: 148px; width: 474px; height: 66px;
    background: var(--teal); clip-path: polygon(0 0, 100% 0, 88.6% 100%, 0 100%);
  }
  .contact-item {
    position: absolute; top: 19px; display: flex; align-items: center; gap: 7px;
    color: var(--white); font-weight: 500; font-size: 17px; letter-spacing: 0.3px;
  }
  .contact-item--phone { left: 45px; }
  .contact-item--place { left: 232px; }
  .contact-item svg { width: 28px; height: 28px; flex: none; }

  /* Back */
  .back-brand {
    position: absolute; left: 0; right: 0; top: 110px;
    display: flex; align-items: center; justify-content: center; gap: 14px;
  }
  .back-brand__mark { width: 22px; height: 22px; background: var(--teal); }
  .back-brand__name {
    color: var(--white); font-weight: 800; font-size: 34px;
    text-transform: uppercase; letter-spacing: 1px; line-height: 1.1; text-align: center;
  }
  .services {
    position: absolute; left: 0; right: 0; top: 299px;
    display: flex; justify-content: center; align-items: center; gap: 8px;
    color: var(--white); font-weight: 500; font-size: 16.5px; letter-spacing: 0.2px;
  }
  .services__dot { width: 7px; height: 7px; border-radius: 50%; background: var(--teal); }
</style>
</head>
<body>

<section class="card card--front">
  <div class="scenery" role="img" aria-label="Black and white silhouette illustration of pine trees and a snowy mountain peak"></div>

  <div class="brand">Birchline Septic Solutions</div>

  <div class="owner">Colin Vandro</div>
  <div class="owner-tab"></div>

  <div class="contact-band">
    <div class="contact-item contact-item--phone">
      <svg viewBox="0 0 28 28" aria-hidden="true">
        <circle cx="14" cy="14" r="12.5" fill="none" stroke="#fff" stroke-width="1.6"/>
        <path d="M10 8.5c-1.3.6-1.8 2-1.2 3.5 1.3 3.2 3.8 5.8 7 7.1 1.5.6 2.9.1 3.5-1.2l-2.4-1.8-1.4 1c-1.7-.8-3-2.1-3.8-3.8l1-1.4z" fill="#fff"/>
      </svg>
      <span>555-214-0387</span>
    </div>
    <div class="contact-item contact-item--place">
      <svg viewBox="0 0 28 28" aria-hidden="true">
        <circle cx="14" cy="14" r="12.5" fill="none" stroke="#fff" stroke-width="1.6"/>
        <path d="M14 7a4.6 4.6 0 0 0-4.6 4.6c0 3.4 4.6 8.4 4.6 8.4s4.6-5 4.6-8.4A4.6 4.6 0 0 0 14 7z" fill="#fff"/>
        <circle cx="14" cy="11.6" r="1.7" fill="#2dbdb8"/>
      </svg>
      <span>Maple Hollow, OH</span>
    </div>
  </div>
</section>

<section class="card card--back">
  <div class="back-brand">
    <span class="back-brand__mark"></span>
    <span class="back-brand__name">Birchline<br>Septic Solutions</span>
  </div>
  <div class="services">
    <span>PUMPING</span><span class="services__dot"></span>
    <span>INSPECTIONS</span><span class="services__dot"></span>
    <span>INSTALLS</span><span class="services__dot"></span>
    <span>REPAIRS</span>
  </div>
</section>

</body>
</html>
```